Business Card Design

We are looking for a business card designed for our landscaping company. We do landscaping installation & Maintenance Services. We would like to see designs that have basic landscaping in background. We also think it is important to have both of our names and phone numbers on the card. We need something that stands out a little whether it is shape of the card or thickness or design.

Business

Bramblewood Yardworks, bramblewoodyard@mailvista.net, Owen Platt 555-273-9104, Daniel Korbin 555-618-3927

```html
<!DOCTYPE html>
<html lang="en">
<head>
<meta charset="utf-8">
<title>Bramblewood Yardworks – Business Card</title>
<link href="https://fonts.googleapis.com/css2?family=Arimo:wght@400;700&display=swap" rel="stylesheet">
<style>
  :root {
    --card-bg: #000000;
    --text-light: #ffffff;
    --accent-green: #86e000;
    --font-main: "Arimo", Arial, sans-serif;
  }
  html, body {
    margin: 0;
    padding: 0;
    width: 1200px;
    height: 700px;
    overflow: hidden;
    background: var(--card-bg);
  }
  .card {
    position: relative;
    width: 1200px;
    height: 700px;
    background: var(--card-bg);
    font-family: var(--font-main);
    color: var(--text-light);
  }
  .brand {
    position: absolute;
    left: 0;
    right: 0;
    top: 292px;
    text-align: center;
  }
  .brand-name {
    margin: 0;
    font-weight: 400;
    font-size: 56px;
    line-height: 1;
    letter-spacing: 0.5px;
    text-transform: uppercase;
    color: var(--text-light);
  }
  .brand-name .highlight {
    color: var(--accent-green);
  }
  .brand-email {
    display: block;
    margin-top: 6px;
    font-size: 35px;
    line-height: 1.15;
    color: var(--accent-green);
  }
  .contacts {
    position: absolute;
    top: 550px;
    left: 0;
    right: 0;
    height: 139px;
  }
  .divider {
    position: absolute;
    left: 599px;
    top: 0;
    width: 2px;
    height: 139px;
    background: var(--accent-green);
  }
  .contact {
    position: absolute;
    top: 50px;
    color: var(--accent-green);
  }
  .contact-left {
    right: 637px;
  }
  .contact-right {
    left: 631px;
  }
  .contact-name {
    display: block;
    font-weight: 700;
    font-size: 34px;
    line-height: 42px;
  }
  .contact-phone {
    display: block;
    font-weight: 400;
    font-size: 36px;
    line-height: 46px;
  }
</style>
</head>
<body>
  <main class="card">
    <header class="brand">
      <h1 class="brand-name">Bramblewood <span class="highlight">Yardworks</span></h1>
      <span class="brand-email">bramblewoodyard@mailvista.net</span>
    </header>
    <section class="contacts">
      <div class="contact contact-left">
        <span class="contact-name">Owen Platt</span>
        <span class="contact-phone">555-273-9104</span>
      </div>
      <div class="divider"></div>
      <div class="contact contact-right">
        <span class="contact-name">Daniel Korbin</span>
        <span class="contact-phone">555-618-3927</span>
      </div>
    </section>
  </main>
</body>
</html>
```